Brightvale cleaning and maintenance company

An expansive website whereby we can advertise our commercial cleaning and maintenance services across a service portfolio of commercial cleaning and property maintenance. Whereby potential skilled resources can deposit there resume so we can collaborate and match candidates to a broad range of cleaning and maintenance jobs/projects.
Updates

Looking for more extensive ideas so the front page can change pictures on it with the focus for Brightvale Commercial Cleaning and Maintenance. Also need to bring in all the portfolios we offer including 1. Equipment Cleaning and Sanitisation Services 2. High pressure gurney and play ground equipment cleaning 3. General Cleaning and Property Facilities Management 4. Project and Recruiting Services, to allow for potential professional cleaners, handy man, mechanics, warehousing resources , electricians to deposit there resume. Most of the designers have stuck with the old portfolio categories , however the portfolio of services we offer has been updated so that needs to be reflected in the website. Also not necessary to use all my original photos I would like the opening page of the website to perhaps be able to change and have different pictures is that possible thank you

```html
<!DOCTYPE html>
<html lang="en">
<head>
<meta charset="utf-8">
<title>Brightvale Commercial Cleaning &amp; Maintenance</title>
<link rel="stylesheet" href="https://fonts.googleapis.com/css2?family=Lato:wght@400;700;900&display=swap">
<style>
:root{
  --blue:#0e3b78;
  --orange:#ff5a13;
  --ink:#1d1d1d;
  --text:#555b63;
  --muted:#7a7f86;
  --white:#ffffff;
}
*{margin:0;padding:0;box-sizing:border-box}
html,body{width:1200px;height:3520px;overflow:hidden}
body{font-family:'Lato',sans-serif;color:var(--text);background:var(--white);position:relative}
.abs{position:absolute}
a{color:inherit;text-decoration:none}

/* header */
.topbar{left:760px;top:0;width:440px;height:42px;background:var(--blue);clip-path:polygon(0 0,100% 0,100% 100%,44px 100%)}
.topbar-call{left:824px;top:6px;display:flex;align-items:center;gap:10px;color:var(--white);font-size:12px;font-weight:700;white-space:nowrap}
.topbar-call strong{font-size:18px;font-weight:700}
.phone-ring{width:30px;height:30px;border:1.5px solid var(--white);border-radius:50%;display:flex;align-items:center;justify-content:center}
.brand{display:flex;align-items:center;gap:10px}
.brand-dot{width:34px;height:34px;border-radius:50%;background:var(--blue)}
.brand-name{font-size:35px;font-weight:400;color:var(--blue);letter-spacing:.2px}
.header-brand{left:112px;top:45px}
.nav{left:463px;top:66px;display:flex;gap:27px;font-size:13px;font-weight:700;color:#333;text-transform:uppercase;white-space:nowrap}
.nav .active{color:var(--orange);position:relative}
.nav .active::before{content:"";position:absolute;left:50%;top:-20px;width:12px;height:12px;margin-left:-6px;border-radius:50%;background:var(--blue)}
.nav-search{left:1074px;top:66px}

/* hero */
.hero{left:0;top:107px;width:1200px;height:501px;background:linear-gradient(110deg,#3c1d12 0%,#8a3a1f 40%,#b0522c 60%,#5a2b1a 100%)}
.hero::after{content:"";position:absolute;inset:0;background:linear-gradient(90deg,rgba(20,10,5,.55),rgba(20,10,5,.1) 60%,rgba(20,10,5,.25))}
.hero-copy{left:112px;top:243px;z-index:2;color:var(--white)}
.hero-title{font-size:45px;font-weight:900;line-height:52px;text-transform:uppercase;white-space:nowrap}
.hero-title span{color:var(--orange)}
.hero-sub{margin-top:6px;font-size:17px;font-weight:700}
.hero-sub span{color:var(--orange)}
.hero-actions{margin-top:18px;display:flex;gap:16px}
.btn{display:inline-flex;align-items:center;justify-content:center;height:42px;padding:0 12px;font-size:14px;font-weight:700;text-transform:uppercase;white-space:nowrap}
.btn-ghost{border:2px solid var(--white);color:var(--white);width:174px}
.btn-solid{background:var(--orange);color:var(--white);width:174px}
.hero-arrow{width:34px;height:34px;background:rgba(0,0,0,.55);display:flex;align-items:center;justify-content:center;z-index:2}

/* about */
.about-img1{left:112px;top:704px;width:283px;height:282px;background:linear-gradient(135deg,#8a4a2e,#c98568 60%,#2e8f86)}
.about-img2{left:210px;top:779px;width:277px;height:276px;border:6px solid var(--white);background:linear-gradient(135deg,#e9e4dd,#b9b8b4 50%,#8d8f92)}
.about-copy{left:560px;top:704px;width:530px}
.eyebrow{border-left:3px solid var(--orange);padding-left:13px;font-size:16px;color:var(--muted);text-transform:uppercase;line-height:20px;padding-top:2px}
.about-heading{border-left:3px solid var(--orange);padding-left:13px;font-size:31px;font-weight:900;color:var(--ink);line-height:44px;text-transform:uppercase;white-space:nowrap;letter-spacing:-.2px}
.about-text{margin-top:12px;font-size:14px;line-height:26px;text-align:justify;color:var(--muted)}
.about-btn{margin-top:16px;width:174px}
.features{margin-top:28px;margin-left:-9px;display:flex}
.feature{display:flex;align-items:center;gap:8px;font-size:14px;line-height:24px;color:#333;text-transform:uppercase}
.feature:nth-child(1){width:205px}
.feature:nth-child(2){width:180px}

/* team band */
.band-staff{left:0;top:1156px;width:599px;height:353px;background:linear-gradient(120deg,#103f80,#0d3a76 60%,#1a4a8a)}
.band-lead{left:599px;top:1156px;width:601px;height:353px;background:linear-gradient(120deg,#ff6a1c,#ff5a13 60%,#f04f0c)}
.band-copy{color:var(--white);width:450px}
.band-copy h2{font-size:25px;font-weight:900;text-transform:uppercase;line-height:30px}
.band-copy p{margin-top:8px;font-size:14px;line-height:26px}
.band-btn{margin-top:22px;height:42px;padding:0 18px;font-size:14px}
.band-btn.on-blue{background:var(--orange);color:var(--white)}
.band-btn.on-orange{background:var(--white);color:var(--orange)}

/* sections */
.section-title{left:0;width:1200px;text-align:center;font-size:36px;font-weight:900;color:var(--ink);text-transform:uppercase}
.section-title::after{content:"";display:block;width:56px;height:3px;background:var(--orange);margin:6px auto 0}
.card{width:254px}
.card-img{height:166px;background:linear-gradient(135deg,#b5b7ba,#7f858c)}
.card-title{margin-top:16px;border-left:3px solid var(--orange);padding-left:13px;font-size:19px;font-weight:400;color:var(--ink);line-height:24px;height:48px}
.card-text{margin-top:14px;font-size:13.5px;line-height:24px;color:var(--text);height:48px;overflow:hidden}
.learn{margin-top:4px;font-size:13.5px;font-weight:700;color:var(--orange);text-transform:uppercase;display:flex;align-items:center;gap:4px}

/* clients */
.clients{left:0;top:2067px;width:1200px;height:462px;background:var(--blue)}
.clients-title{color:var(--white)}
.clients-text{left:230px;top:2216px;width:740px;text-align:center;color:var(--white);font-size:14px;font-weight:700;line-height:26px}
.client-box{width:237px;height:99px;background:var(--white);display:flex;align-items:center;justify-content:center;gap:8px;font-size:19px;font-weight:700;color:var(--blue)}
.client-mark{width:14px;height:14px;background:var(--orange);border-radius:50%}
.client-name{width:237px;text-align:center;color:var(--white);font-size:14px;font-weight:900;text-transform:uppercase}

/* blog */
.post{width:313px}
.post-img{height:183px}
.post-meta{margin-top:14px;display:flex;justify-content:space-between;font-size:14px}
.post-meta .tag{color:var(--orange);text-transform:uppercase}
.post-meta .date{color:#444}
.post-title{margin-top:10px;font-size:17px;font-weight:700;color:var(--ink)}
.post-text{margin-top:10px;font-size:13.5px;line-height:26px;color:var(--muted);word-break:break-all}

/* footer */
.footer{left:0;top:3117px;width:1200px;height:403px;background:var(--blue)}
.footer-brand .brand-dot{background:var(--white)}
.footer-brand .brand-name{color:var(--white)}
.footer-col{color:var(--white)}
.footer-col h3{border-left:2px solid var(--orange);padding-left:6px;font-size:18px;font-weight:700;line-height:22px}
.footer-col p,.footer-col li{font-size:14px;line-height:22px}
.footer-col ul{list-style:none;margin-top:10px}
.footer-col li{line-height:28px}
.hours{display:grid;grid-template-columns:173px 1fr;font-size:14px;line-height:20px}
.estimate-phone{margin-top:18px;font-size:20px !important;font-weight:700}
.estimate-btn{margin-top:22px;width:166px;height:40px;border:2px solid var(--white);display:flex;align-items:center;justify-content:center;font-size:15px;text-transform:uppercase}
.gallery{left:828px;top:3244px;display:grid;grid-template-columns:128px 128px;grid-template-rows:90px 90px;gap:6px}
.gallery div:nth-child(1){background:linear-gradient(135deg,#d7b98a,#8a9aa8)}
.gallery div:nth-child(2){background:linear-gradient(135deg,#cfd6df,#2f6fb8)}
.gallery div:nth-child(3){background:linear-gradient(135deg,#3a66b0,#f0c6b0)}
.gallery div:nth-child(4){background:linear-gradient(135deg,#b8a890,#6f6a60)}
.footer-rule{left:112px;top:3458px;width:976px;height:1px;background:rgba(255,255,255,.5)}
.copyright{left:0;top:3476px;width:1200px;text-align:center;color:var(--white);font-size:14px}
</style>
</head>
<body>

<!-- header -->
<div class="abs topbar"></div>
<div class="abs topbar-call">
  <span class="phone-ring"><svg width="14" height="14" viewBox="0 0 24 24"><path fill="#fff" d="M6.6 10.8a15.5 15.5 0 0 0 6.6 6.6l2.2-2.2a1 1 0 0 1 1-.25 11.4 11.4 0 0 0 3.6.57 1 1 0 0 1 1 1V20a1 1 0 0 1-1 1A17 17 0 0 1 3 4a1 1 0 0 1 1-1h3.5a1 1 0 0 1 1 1c0 1.25.2 2.45.57 3.57a1 1 0 0 1-.25 1z"/></svg></span>
  <span>Call us Today : <strong>+1 555 010 2040</strong></span>
</div>
<div class="abs header-brand brand"><span class="brand-dot"></span><span class="brand-name">Brightvale</span></div>
<nav class="abs nav">
  <a class="active">Home</a><a>Services</a><a>About Us</a><a>Our People</a><a>Safety &amp; Compliance</a><a>Contact</a>
</nav>
<svg class="abs nav-search" width="14" height="14" viewBox="0 0 24 24"><circle cx="10" cy="10" r="7" fill="none" stroke="#333" stroke-width="3"/><path d="M15 15l6 6" stroke="#333" stroke-width="3"/></svg>

<!-- hero -->
<section class="abs hero" role="img" aria-label="Technician pressure-washing a terracotta tiled roof"></section>
<div class="abs hero-copy">
  <h1 class="hero-title">We are <span>always</span><br>ready to services</h1>
  <p class="hero-sub">For Immediate Services Dial <span>+1 555 010 2040</span></p>
  <div class="hero-actions"><a class="btn btn-ghost">View more details</a><a class="btn btn-solid">Our portfolio</a></div>
</div>
<a class="abs hero-arrow" style="left:41px;top:303px"><svg width="10" height="10" viewBox="0 0 10 10"><path d="M7 1L3 5l4 4" fill="none" stroke="#fff" stroke-width="1.6"/></svg></a>
<a class="abs hero-arrow" style="left:1125px;top:303px"><svg width="10" height="10" viewBox="0 0 10 10"><path d="M3 1l4 4-4 4" fill="none" stroke="#fff" stroke-width="1.6"/></svg></a>

<!-- about -->
<div class="abs about-img1" role="img" aria-label="Hand wiping a glass clean"></div>
<div class="abs about-img2" role="img" aria-label="Clean stainless steel commercial sink"></div>
<div class="abs about-copy">
  <p class="eyebrow">About Brightvale</p>
  <h2 class="about-heading">We build for your comfort</h2>
  <p class="about-text">Lorem ipsum dolor sit amet, consectetur adipiscing elit, sed do eiusmod tempor incididunt ut labore et dolore magna aliqua. Ut enim ad minim veniam, quis nostrud exercitation ullamco laboris nisi ut aliquip ex ea commodo consequat. Duis aute irure dolor in reprehenderit in voluptate velit esse cillum dolore eu fugiat nulla pariatur. Excepteur sint occaecat cupidatat non proident, sunt in culpa qui officia deserunt mollit anim id est laborum.</p>
  <a class="btn btn-solid about-btn">Our portfolio</a>
  <div class="features">
    <div class="feature">
      <svg width="40" height="40" viewBox="0 0 40 40" fill="none" stroke="#333" stroke-width="1.6"><circle cx="22" cy="22" r="13"/><path d="M22 14v8l6 4M17 6h10M2 18h7M4 24h5M6 30h4"/></svg>
      <span>Ontime at<br>services</span>
    </div>
    <div class="feature">
      <svg width="40" height="40" viewBox="0 0 40 40" fill="none" stroke="#333" stroke-width="1.6"><path d="M6 34L26 14M22 8a7 7 0 0 0 10 10l-4-1-3-3-1-4zM8 6l6 6-2 2-6-6zM20 22l12 12-3 3-12-12"/></svg>
      <span>24/7<br>services</span>
    </div>
    <div class="feature">
      <svg width="40" height="40" viewBox="0 0 40 40" fill="none" stroke="#333" stroke-width="1.6"><circle cx="20" cy="16" r="12"/><circle cx="20" cy="16" r="7"/><path d="M12 25l-5 10 5-1 3 4 4-9M28 25l5 10-5-1-3 4-4-9"/></svg>
      <span>Verified<br>professionals</span>
    </div>
  </div>
</div>

<!-- team band -->
<section class="abs band-staff" role="img" aria-label="Cleaning staff at work, blue tint"></section>
<section class="abs band-lead" role="img" aria-label="Leadership team meeting, orange tint"></section>
<div class="abs band-copy" style="left:110px;top:1244px">
  <h2>Our staff</h2>
  <p>We are proud of our team. The majority of staff has been with the company for many years. As a result, the understanding of our clients and our bench strength of cleaning professionals is extremely strong.</p>
  <a class="btn band-btn on-blue">Learn more &#10148;</a>
</div>
<div class="abs band-copy" style="left:709px;top:1244px;width:460px">
  <h2>Our leadership team</h2>
  <p>Our leadership team hold themselves accountable to living our purpose, achieving our vision, supporting our people and ensuring every part of our business is focused on what we value and the quality</p>
  <a class="btn band-btn on-orange">Learn more &#10148;</a>
</div>

<!-- services -->
<h2 class="abs section-title" style="top:1594px">Our services</h2>
<article class="abs card" style="left:74px;top:1664px">
  <div class="card-img" role="img" aria-label="Soft-serve machine being sanitised"></div>
  <h3 class="card-title">Equipment Cleaning &amp; Sanitisation</h3>
  <p class="card-text">Full cleaning, sanitising and tune up kit service for food service equipment</p>
  <a class="learn">Learn more &#10148;</a>
</article>
<article class="abs card" style="left:339px;top:1664px">
  <div class="card-img" role="img" aria-label="Colourful playground equipment" style="background:linear-gradient(135deg,#e3b04a,#3f5fa8)"></div>
  <h3 class="card-title">Gurney &amp; Playground Cleaning</h3>
  <p class="card-text">High pressure gurney cleaning of hard surfaces and playground equipment</p>
  <a class="learn">Learn more &#10148;</a>
</article>
<article class="abs card" style="left:606px;top:1664px">
  <div class="card-img" role="img" aria-label="Commercial building interior" style="background:linear-gradient(135deg,#d5d2cc,#6b6a68)"></div>
  <h3 class="card-title">General &amp; Facilities Management</h3>
  <p class="card-text">General cleaning plus property and facilities management for your sites</p>
  <a class="learn">Learn more &#10148;</a>
</article>
<article class="abs card" style="left:871px;top:1664px">
  <div class="card-img" role="img" aria-label="Tradespeople on a project site" style="background:linear-gradient(135deg,#6f6a66,#bdbcba)"></div>
  <h3 class="card-title">Project &amp; Recruiting Services</h3>
  <p class="card-text">Cleaners, handymen, mechanics and electricians: submit your resume</p>
  <a class="learn">Upload resume &#10148;</a>
</article>

<!-- clients -->
<section class="abs clients"></section>
<h2 class="abs section-title clients-title" style="top:2150px">Clients</h2>
<p class="abs clients-text">Brightvale has established a strong reputation as being reliable, responsive and dedicated to fulfilling our customers and partners cleaning service needs.</p>
<div class="abs client-box" style="left:191px;top:2303px"><span class="client-mark"></span>Northbay</div>
<div class="abs client-box" style="left:474px;top:2303px"><span class="client-mark"></span>Golden Crest</div>
<div class="abs client-box" style="left:757px;top:2303px"><span class="client-mark"></span>Harbor Burger</div>
<p class="abs client-name" style="left:191px;top:2421px">Northbay Beverages</p>
<p class="abs client-name" style="left:474px;top:2421px">Golden Crest Grill</p>
<p class="abs client-name" style="left:757px;top:2421px">Harbor Burger Co.</p>

<!-- blog -->
<h2 class="abs section-title" style="top:2613px">Our latest blog</h2>
<article class="abs post" style="left:111px;top:2696px">
  <div class="post-img" role="img" aria-label="Business meeting" style="background:linear-gradient(135deg,#e5eaf0,#33475e)"></div>
  <div class="post-meta"><span class="tag">Blog</span><span class="date">Jan 15th 2020</span></div>
  <h3 class="post-title">Lorem ipsum dolor sit amet, conse</h3>
  <p class="post-text">Lorem ipsum dolor sit amet, consectetur adipiscing elit, sed do eiusmod tempor incididunt ut labore et dolore magna aliqua.</p>
</article>
<article class="abs post" style="left:443px;top:2696px">
  <div class="post-img" role="img" aria-label="Office worker holding a folder" style="background:linear-gradient(135deg,#f2f2f2,#a9b1bb)"></div>
  <div class="post-meta"><span class="tag">Blog</span><span class="date">Jan 15th 2020</span></div>
  <h3 class="post-title">Lorem ipsum dolor sit amet, conse</h3>
  <p class="post-text">Lorem ipsum dolor sit amet, consectetur adipiscing elit, sed do eiusmod tempor incididunt ut labore et dolore magna aliqua.</p>
</article>
<article class="abs post" style="left:775px;top:2696px">
  <div class="post-img" role="img" aria-label="Machine parts laid out for cleaning" style="background:linear-gradient(135deg,#3a3a3c,#c9b27a 60%,#8c8e92)"></div>
  <div class="post-meta"><span class="tag">Blog</span><span class="date">Jan 15th 2020</span></div>
  <h3 class="post-title">Lorem ipsum dolor sit amet, conse</h3>
  <p class="post-text">Lorem ipsum dolor sit amet, consectetur adipiscing elit, sed do eiusmod tempor incididunt ut labore et dolore magna aliqua.</p>
</article>

<!-- footer -->
<footer class="abs footer"></footer>
<div class="abs footer-brand brand" style="left:112px;top:3190px"><span class="brand-dot"></span><span class="brand-name">Brightvale</span></div>
<div class="abs footer-col" style="left:112px;top:3246px;width:270px">
  <p>Lorem ipsum dolor sit amet, conse ctetur adipiscing elit, sed do eius mod tempor incididunt ut labore</p>
  <h3 style="margin-top:12px">Work Days</h3>
  <div class="hours" style="margin-top:10px"><span>Mon - sat</span><span>09am - 05pm</span><span>Sunday</span><span>Closed</span></div>
</div>
<div class="abs footer-col" style="left:435px;top:3200px">
  <h3>Quick Links</h3>
  <ul><li>Home</li><li>Services</li><li>About us</li><li>Our People</li><li>Safety &amp; Compliance</li><li>Contact</li></ul>
</div>
<div class="abs footer-col" style="left:616px;top:3200px;width:180px">
  <h3>Get Free Estimate</h3>
  <p class="estimate-phone">123-555-0190</p>
  <p style="margin-top:8px">Our online scheduling and payment system is safe.</p>
  <a class="estimate-btn">Request form</a>
</div>
<div class="abs footer-col" style="left:828px;top:3200px"><h3>Gallery</h3></div>
<div class="abs gallery">
  <div role="img" aria-label="Cleaning crew outdoors"></div>
  <div role="img" aria-label="Drink dispensing machines"></div>
  <div role="img" aria-label="Children at a playground"></div>
  <div role="img" aria-label="Kitchen equipment"></div>
</div>
<div class="abs footer-rule"></div>
<p class="abs copyright">(c) 2020 Brightvale | All Rights Reserved | Terms and Conditions</p>

</body>
</html>
```